A website for a Maltese Law Firm

Our law firm needs a website to further its business. The site should have a simple yet effective design. We would need the following sections: About us, Practice Areas, About Malta, Contact. These should be further split as follows:

About us: Our firm, Our values, What others say, Offices

Practice Areas: Crimimal, Citizenship & Residence, Sovereign Patron Pathway, Criminal Defence, Civil Litigation, Arbitration and ADR, Commercial and Corporate, Media Law.

About Malta: just one section.

Contact: Just one section

We would also need a news feed at the front of the site to include latest news regarding our cases.

At the bottom we need a section for our Terms and a Privacy Statement.

Our logo is being attached.

Target Market(s)

All clients looking for legal assistance in Malta

Industry/Entity Type

Legal

Coding

Coded - Design and coding required

Number of Pages Required

1 page

Requirements
Must have
• It must be simple yet striking.

```html
<!DOCTYPE html>
<html lang="en">
<head>
<meta charset="utf-8">
<title>Calleja &amp; Borg Advocates</title>
<link href="https://fonts.googleapis.com/css2?family=Cinzel:wght@400;700&family=Lato:ital,wght@0,400;0,700;1,400&family=Montserrat:wght@400;600&display=swap" rel="stylesheet">
<style>
:root{
  --orange:#f7941d;
  --ink:#2b2b2b;
  --text:#555;
  --muted:#8d8d8d;
  --light:#ebebeb;
  --panel:#9e9e9e;
  --footer:#8a8a8a;
  --bar:#2a2a2a;
  --white:#fff;
}
*{box-sizing:border-box;margin:0;padding:0}
html,body{width:1200px;height:3681px;overflow:hidden}
body{font-family:'Lato',sans-serif;color:var(--text);background:var(--white);position:relative}
.serif{font-family:'Cinzel',serif}
section,header,footer{position:absolute;left:0;width:1200px}
.abs{position:absolute}

/* nav */
.site-header{top:0;height:69px;background:var(--white)}
.brand{left:98px;top:0;width:275px;height:81px;background:var(--ink);border-bottom:4px solid var(--orange);display:flex;align-items:center;justify-content:center;z-index:2}
.brand span{font-family:'Cinzel',serif;color:var(--white);font-size:23px;letter-spacing:1px}
.nav-link{top:25px;font-family:'Cinzel',serif;font-size:14px;color:var(--ink)}
.nav-link.active{color:var(--orange)}
.nav-search{left:1070px;top:18px;width:32px;height:32px;background:var(--orange)}

/* hero */
.hero{top:69px;height:528px}
.hero-photo{position:absolute;inset:0;background:linear-gradient(90deg,#1d1a17 0%,#3b322b 35%,#5a5552 60%,#2f3239 100%)}
.hero-title{left:98px;top:187px;font-family:'Cinzel',serif;color:var(--white);font-size:54px;line-height:62px;text-align:center}

/* about */
.about{top:597px;height:606px;background:var(--light)}
.section-title{font-family:'Cinzel',serif;color:var(--ink);font-size:36px}
.about .section-title{left:0;width:1200px;top:82px;text-align:center}
.title-rule{top:105px;height:2px;width:130px;background:var(--ink)}
.feature{top:170px;width:250px;text-align:center}
.feature .ring{width:134px;height:134px;margin:0 auto;border:2px solid #c9c9c9;border-radius:50%;display:flex;align-items:center;justify-content:center}
.feature.active .ring{border-color:var(--orange)}
.feature h3{margin-top:38px;font-family:'Montserrat',sans-serif;font-weight:400;font-size:21px;color:var(--ink)}
.feature.active h3{color:var(--orange)}
.feature p{margin-top:14px;font-size:14px;line-height:21px;color:#666}
.btn-grey{left:488px;top:493px;width:224px;height:46px;background:#6e6e6e;color:var(--white);font-family:'Cinzel',serif;font-size:20px;display:flex;align-items:center;justify-content:center}

/* practice */
.practice{top:1203px;height:932px;background:var(--white)}
.practice .section-title{left:98px;top:70px;font-size:34px}
.practice .intro{left:98px;top:134px;width:1000px;font-size:14px;line-height:22px;color:#666}
.card{width:241px}
.card .thumb{height:158px;border:4px solid #eee}
.card h4{margin-top:32px;font-family:'Montserrat',sans-serif;font-weight:600;font-size:14px;color:var(--ink)}
.card p{margin-top:8px;font-size:13px;line-height:20px;color:var(--muted)}
.btn-orange{background:var(--orange);color:var(--white);font-family:'Cinzel',serif;font-size:18px;display:flex;align-items:center;justify-content:center}

/* malta */
.malta{top:2135px;height:557px}
.malta-photo{position:absolute;inset:0;background:linear-gradient(90deg,#2a2622 0%,#4a423b 45%,#3a3532 70%,#2b2a29 100%)}
.malta h2{left:98px;top:110px;font-family:'Cinzel',serif;font-size:34px;color:var(--white)}
.malta p{left:98px;top:192px;width:432px;font-size:17px;line-height:22px;color:var(--white)}

/* testimonial + contact */
.split{top:2692px;height:518px}
.testimonial{left:0;top:0;width:596px;height:518px;background:#ececec}
.testimonial h2{left:98px;top:80px;font-family:'Cinzel',serif;font-size:32px;color:var(--ink)}
.quote{left:128px;top:155px;width:410px;font-style:italic;font-size:14px;line-height:22px;color:#666}
.qmark{font-family:'Cinzel',serif;font-size:40px;color:var(--ink)}
.avatar{left:140px;top:299px;width:84px;height:84px;border-radius:50%;background:linear-gradient(#d9d9d9,#9a9a9a);border:3px solid var(--white)}
.stars{left:98px;top:389px;width:170px;text-align:center;color:var(--orange);font-size:15px;letter-spacing:2px}
.person{left:98px;top:413px;width:170px;text-align:center;font-family:'Montserrat',sans-serif;font-size:13px;color:var(--ink)}
.years{left:98px;top:432px;width:170px;text-align:center;font-size:12px;color:var(--muted)}
.contact{left:596px;top:0;width:604px;height:518px;background:var(--panel)}
.contact h2{left:67px;top:80px;font-family:'Cinzel',serif;font-size:34px;color:var(--white)}
.field{left:67px;width:331px;border:1px solid #c6c6c6;color:#eee;font-size:13px;padding:9px 12px}

/* follow */
.follow{top:3210px;height:135px;background:var(--white)}
.follow h2{left:142px;top:50px;font-family:'Cinzel',serif;font-size:32px;color:#555;letter-spacing:2px}
.social{top:50px;display:flex;gap:14px}
.social .sq{width:32px;height:32px}
.social b{display:block;font-weight:400;font-size:17px}
.social small{display:block;font-size:12px;color:var(--muted)}

/* footer */
.site-footer{top:3345px;height:302px;background:var(--footer);color:var(--white)}
.site-footer h5{left:98px;top:62px;font-family:'Cinzel',serif;font-size:17px;font-weight:400}
.map-link{font-size:12px}
.foot-brand{left:452px;top:78px;width:236px;text-align:center;font-family:'Cinzel',serif;font-size:23px;border-bottom:2px solid var(--white);padding-bottom:2px}
.address{left:420px;top:132px;width:300px;text-align:center;font-family:'Cinzel',serif;font-size:17px;line-height:27px}
.contact-row{left:798px;display:flex;align-items:center;gap:18px;font-family:'Cinzel',serif;font-size:17px}
.bottom-bar{top:3647px;height:34px;background:var(--bar);color:var(--white);font-size:11px}
.bottom-bar span{position:absolute;top:11px}
</style>
</head>
<body>

<header class="site-header">
  <div class="abs brand"><span>Calleja &amp; Borg</span></div>
  <a class="abs nav-link active" style="left:463px">Home</a>
  <a class="abs nav-link" style="left:552px">About Us</a>
  <a class="abs nav-link" style="left:666px">Practice Areas</a>
  <a class="abs nav-link" style="left:824px">About Malta</a>
  <a class="abs nav-link" style="left:967px">Contact</a>
  <div class="abs nav-search">
    <svg width="32" height="32" viewBox="0 0 32 32"><circle cx="14" cy="14" r="6" fill="none" stroke="#fff" stroke-width="2"/><line x1="18.5" y1="18.5" x2="23" y2="23" stroke="#fff" stroke-width="2.4"/></svg>
  </div>
</header>

<section class="hero">
  <div class="hero-photo" role="img" aria-label="Photograph of a lawyer in a dark suit and striped tie in front of bookshelves"></div>
  <h1 class="abs hero-title">Calleja &amp; Borg<br>Advocates</h1>
  <svg class="abs" style="left:603px;top:430px" width="20" height="36" viewBox="0 0 20 36"><rect x="2" y="2" width="16" height="26" rx="8" fill="none" stroke="#fff" stroke-width="2"/><line x1="10" y1="8" x2="10" y2="13" stroke="#fff" stroke-width="2"/><line x1="10" y1="30" x2="10" y2="35" stroke="#fff" stroke-width="1.5"/></svg>
</section>

<section class="about">
  <div class="abs title-rule" style="left:372px"></div>
  <h2 class="abs section-title">About Us</h2>
  <div class="abs title-rule" style="left:698px"></div>

  <div class="abs feature active" style="left:76px">
    <div class="ring" style="background:var(--white)">
      <svg width="64" height="56" viewBox="0 0 64 56" fill="none" stroke="#f7941d" stroke-width="3"><line x1="32" y1="4" x2="32" y2="48"/><line x1="10" y1="12" x2="54" y2="12"/><path d="M10 12 L2 30 H18 Z"/><path d="M54 12 L46 30 H62 Z"/><line x1="18" y1="50" x2="46" y2="50"/></svg>
    </div>
    <h3>Our Firm</h3>
    <p>Duis aute irure dolor in<br>reprehenderit in voluptate velit<br>esse cillum</p>
  </div>
  <div class="abs feature" style="left:339px">
    <div class="ring"><svg width="60" height="56" viewBox="0 0 60 56" fill="none" stroke="#777" stroke-width="2.5"><rect x="8" y="34" width="8" height="16"/><rect x="22" y="26" width="8" height="24"/><rect x="36" y="18" width="8" height="32"/><polyline points="6,26 22,14 34,18 52,4"/><polyline points="44,4 52,4 52,12"/></svg></div>
    <h3>Our Values</h3>
    <p>Duis aute irure dolor in<br>reprehenderit in voluptate velit<br>esse cillum</p>
  </div>
  <div class="abs feature" style="left:606px">
    <div class="ring"><svg width="56" height="56" viewBox="0 0 56 56" fill="none" stroke="#777" stroke-width="2.5"><path d="M8 10 H48 V38 H26 L14 48 V38 H8 Z"/><line x1="16" y1="20" x2="40" y2="20"/><line x1="16" y1="28" x2="34" y2="28"/></svg></div>
    <h3>What Others Say</h3>
    <p>Duis aute irure dolor in<br>reprehenderit in voluptate velit<br>esse cillum</p>
  </div>
  <div class="abs feature" style="left:871px">
    <div class="ring"><svg width="60" height="56" viewBox="0 0 60 56" fill="none" stroke="#777" stroke-width="2.5"><rect x="6" y="28" width="48" height="20"/><rect x="22" y="34" width="16" height="8"/><rect x="18" y="10" width="24" height="16"/></svg></div>
    <h3>Offices</h3>
    <p>Duis aute irure dolor in<br>reprehenderit in voluptate velit<br>esse cillum</p>
  </div>
  <div class="abs btn-grey">Learn More</div>
</section>

<section class="practice">
  <h2 class="abs section-title">Practice Areas</h2>
  <p class="abs intro">Lorem ipsum dolor sit amet, consectetur adipisicing elit, sed do eiusmod tempor incididunt ut labore et dolore magna aliqua. Ut enim ad minim veniam, quis nostrud exercitation</p>

  <div class="abs card" style="left:98px;top:215px"><div class="thumb" role="img" aria-label="Photograph of handcuffed hands" style="background:linear-gradient(#7a6a60,#3b3030)"></div><h4>Crimimal</h4><p>Duis aute irure dolor in volupt<br>ate velit esse cillum...</p></div>
  <div class="abs card" style="left:350px;top:215px"><div class="thumb" role="img" aria-label="Photograph of a woman holding a national flag" style="background:linear-gradient(90deg,#5c8a3c,#d9cfc2,#a84b3c)"></div><h4>Citizenship &amp; Residence</h4><p>Duis aute irure dolor in volupt<br>ate velit esse cillum...</p></div>
  <div class="abs card" style="left:603px;top:215px"><div class="thumb" role="img" aria-label="Photograph of stacked gold coins" style="background:linear-gradient(#a9b7c9,#d3a445)"></div><h4>Sovereign Patron Pathway</h4><p>Duis aute irure dolor in volupt<br>ate velit esse cillum...</p></div>
  <div class="abs card" style="left:855px;top:215px"><div class="thumb" role="img" aria-label="Photograph of a judge's gavel and law books" style="background:linear-gradient(#8a5a30,#3a2416)"></div><h4>Criminal Defence</h4><p>Duis aute irure dolor in volupt<br>ate velit esse cillum...</p></div>

  <div class="abs card" style="left:98px;top:502px"><div class="thumb" role="img" aria-label="Illustration of a chain with a gold padlock" style="background:linear-gradient(#f2f2f2,#c9a23a)"></div><h4>Civil Litigation</h4><p>Duis aute irure dolor in volupt<br>ate velit esse cillum...</p></div>
  <div class="abs card" style="left:350px;top:502px"><div class="thumb" role="img" aria-label="Photograph of a gavel resting on legal papers" style="background:linear-gradient(#6b3b22,#d6c9ad)"></div><h4>Arbitration and ADR</h4><p>Duis aute irure dolor in volupt<br>ate velit esse cillum...</p></div>
  <div class="abs card" style="left:603px;top:502px"><div class="thumb" role="img" aria-label="Photograph of business people shaking hands" style="background:linear-gradient(#e8e8e8,#2e2e33)"></div><h4>Commercial and Corporate</h4><p>Duis aute irure dolor in volupt<br>ate velit esse cillum...</p></div>
  <div class="abs card" style="left:855px;top:502px"><div class="thumb" role="img" aria-label="Photograph of a magnifying glass on newspapers" style="background:linear-gradient(#4b2e20,#a0704a)"></div><h4>Media Law</h4><p>Duis aute irure dolor in volupt<br>ate velit esse cillum...</p></div>

  <div class="abs btn-orange" style="left:98px;top:812px;width:290px;height:49px">View All practices</div>
</section>

<section class="malta">
  <div class="malta-photo" role="img" aria-label="Photograph of a smiling businesswoman holding a folder in front of stone columns"></div>
  <h2 class="abs">About Malta</h2>
  <p class="abs">Lorem ipsum dolor sit amet, consectetur adipisicing elit, sed do eiusmod tempor incididunt ut labore et dolore magna aliqua. Ut enim ad minim veniam, quis nostrud exercitation ullamco laboris nisi ut aliquip ex ea commodo consequat. Duis aute irure dolor in reprehenderit in voluptate velit esse cillum dolore eu fugiat nulla pariatur.</p>
  <div class="abs btn-orange" style="left:98px;top:402px;width:204px;height:50px">Our Values</div>
</section>

<section class="split">
  <div class="abs testimonial">
    <h2 class="abs">What Others Say</h2>
    <span class="abs qmark" style="left:96px;top:150px">&ldquo;</span>
    <p class="abs quote">Lorem ipsum dolor sit amet, consectetur adipisicing elit, sed do eiusmod tempor incididunt ut labore et dolore magna aliqua. Ut enim ad minim veniam, quis nostrud exercitation ullamco laboris nisi ut aliquip ex ea commodo consequat. Duis aute irure dolor in reprehenderit.</p>
    <span class="abs qmark" style="left:348px;top:238px">&rdquo;</span>
    <div class="abs avatar" role="img" aria-label="Portrait photograph of the client"></div>
    <div class="abs stars">★★★★★</div>
    <div class="abs person">DANIEL MIFSUD</div>
    <div class="abs years">22 years</div>
  </div>
  <div class="abs contact">
    <h2 class="abs">Contact</h2>
    <div class="abs field" style="top:160px;height:37px">Your Name</div>
    <div class="abs field" style="top:216px;height:37px">Your Email</div>
    <div class="abs field" style="top:270px;height:118px">Your Massage</div>
    <div class="abs btn-orange" style="left:67px;top:405px;width:203px;height:47px">Subscribe</div>
  </div>
</section>

<section class="follow">
  <h2 class="abs">Follow Us</h2>
  <div class="abs social" style="left:410px"><div class="sq" style="background:#3b5998"></div><div><b style="color:#3b5998">Find Us</b><small>on Circlebook</small></div></div>
  <div class="abs social" style="left:582px"><div class="sq" style="background:#f7a11a"></div><div><b style="color:#f7a11a">Subscribe</b><small>to RSS Feed</small></div></div>
  <div class="abs social" style="left:753px"><div class="sq" style="background:#cb2027"></div><div><b style="color:#cb2027">Follow Us</b><small>on Pinboard Hub</small></div></div>
  <div class="abs social" style="left:925px"><div class="sq" style="background:#2aa9e0"></div><div><b style="color:#2aa9e0">Follow Us</b><small>on Chirper</small></div></div>
</section>

<footer class="site-footer">
  <h5 class="abs">Site Map</h5>
  <span class="abs map-link" style="left:98px;top:108px">Home</span>
  <span class="abs map-link" style="left:98px;top:132px">About us</span>
  <span class="abs map-link" style="left:98px;top:157px">Practice Areas</span>
  <span class="abs map-link" style="left:98px;top:181px">About Malta</span>
  <span class="abs map-link" style="left:98px;top:206px">Contact</span>
  <span class="abs map-link" style="left:263px;top:108px">FAQs</span>
  <span class="abs map-link" style="left:263px;top:132px">Our Firm</span>
  <span class="abs map-link" style="left:263px;top:157px">Our Values</span>
  <span class="abs map-link" style="left:263px;top:181px">Latest news</span>
  <span class="abs map-link" style="left:263px;top:206px">Office</span>

  <div class="abs foot-brand">Calleja &amp; Borg</div>
  <div class="abs address">22/7, Merchant Row, Valletta<br>118, Orchard Street, Birkirkara</div>

  <div class="abs contact-row" style="top:104px"><svg width="24" height="24" viewBox="0 0 24 24" fill="none" stroke="#fff" stroke-width="1.6"><path d="M5 3 L9 3 L11 8 L8 10 C9 13 11 15 14 16 L16 13 L21 15 L21 19 C21 20 20 21 19 21 C10 21 3 14 3 5 C3 4 4 3 5 3 Z"/></svg>(356) 2000 1100 (Birkirkara)</div>
  <div class="abs contact-row" style="top:152px"><svg width="24" height="24" viewBox="0 0 24 24" fill="none" stroke="#fff" stroke-width="1.6"><path d="M5 3 L9 3 L11 8 L8 10 C9 13 11 15 14 16 L16 13 L21 15 L21 19 C21 20 20 21 19 21 C10 21 3 14 3 5 C3 4 4 3 5 3 Z"/></svg>(356) 2000 2200 (Valletta)</div>
  <div class="abs contact-row" style="top:199px"><svg width="24" height="24" viewBox="0 0 24 24" fill="none" stroke="#fff" stroke-width="1.6"><rect x="6" y="3" width="12" height="6"/><rect x="3" y="9" width="18" height="8"/><rect x="6" y="14" width="12" height="7"/></svg>(356) 2000 3300</div>
  <div class="abs contact-row" style="top:244px;font-family:'Lato',sans-serif;font-size:12px"><svg width="24" height="24" viewBox="0 0 24 24" fill="none" stroke="#fff" stroke-width="1.6"><rect x="3" y="6" width="18" height="12"/><polyline points="3,6 12,13 21,6"/></svg><span style="color:var(--orange)">info@callejaborg.example</span></div>
</footer>

<div class="abs bottom-bar" style="left:0;width:1200px">
  <span style="left:98px">Home</span>
  <span style="left:150px">Latest news</span>
  <span style="left:236px">About</span>
  <span style="left:290px">Site Map</span>
  <span style="left:358px">Advocates</span>
  <span style="left:436px">Terms And Privacy</span>
  <span style="left:808px">Copyright 2016 Harbour Web Studio &nbsp;|&nbsp; All Rights Reserved</span>
</div>

</body>
</html>
```